Sales and Marketing company needs website page graphics

We are redesigning our website and need graphics for the top of our solution pages. Currently you’ll see that there is one photo graphic with a differing color screen for each section. We’re looking for photo graphic designs that will represent each unique solution section (lead generation, prospecting, hiring) and fit within the overall website design. We will add the section title text to the photo graphic. This will be a total of 3 graphics.

This is a link to the working website redesign: http://trevindale.com/brunexatemp/
The content on the working redesign page is correct and will give you a good sense for how we talk about each solution. You’ll notice that the redesign is text heavy. We’ll work on that next.

Our current website is: www.brunexa.com
You’ll get a good sense for our designs on our blog: http://www.brunexa.com/blog

As a company, our goal is to help our clients get more customers. We do that through consulting, training and outsourced lead generation. Key words that describe us: flexible, responsive, and fun. (Although you don’t see that in our current website, hopefully it comes through more on our blog – and then on our new website!)

We will need the graphic design in high resolution formats. We will own the copyright and intellectual property.

North American companies that earn $750K - $85M in annual revenue selling to other businesses. Most are in the computer technology industry.

Business Service

Sans Serif

• Fit the design of the website.
• If there are people in the graphics, I like to see diversity: Asian,Black, Latin, Caucasian, men and women.
• Be creative, not like every other graphic you see on a website. We are a woman owned business and Marisol is well known. We don't want to feel generic. Potentially be something we can use elements of for other graphics.
• We really want your expertise and this is our first project with Artvoyle .
• We will insert the solution section text, so there wouldn't be the text unless it's part of the graphic design.

```html
<!DOCTYPE html>
<html lang="en">
<head>
<meta charset="utf-8">
<title>Brunexa Group – Hiring and Onboarding</title>
<link href="https://fonts.googleapis.com/css2?family=Lato:wght@400;700;900&display=swap" rel="stylesheet">
<style>
  :root {
    --purple: #5a2d82;
    --purple-dark: #4a2270;
    --green-active: #7cbc44;
    --teal: #1d6670;
    --grey: #8c8c8c;
    --grey-light: #c9c9c9;
    --text: #4a4a4a;
    --white: #ffffff;
    --hero-dark: #23402a;
    --hero-mid: #5f8f5c;
    --hero-light: #c8e4b4;
  }
  * { box-sizing: border-box; margin: 0; padding: 0; }
  html, body { width: 1200px; height: 758px; overflow: hidden; background: var(--white); }
  body { font-family: "Lato", Arial, sans-serif; color: var(--text); }

  .page { width: 1200px; height: 758px; position: relative; }

  .site-header {
    height: 72px; display: flex; align-items: center; justify-content: space-between;
    padding: 0 70px 0 88px;
  }
  .brand { display: flex; align-items: center; gap: 10px; }
  .brand-mark { width: 14px; height: 14px; background: var(--purple); }
  .brand-name { font-weight: 900; font-size: 34px; color: var(--purple); letter-spacing: -0.5px; }
  .header-links { display: flex; align-items: center; gap: 140px; }
  .speaker-link { font-size: 12px; font-weight: 700; color: var(--purple); letter-spacing: 0.3px; text-decoration: none; }
  .phone { font-size: 17px; color: var(--purple); }

  .main-nav {
    height: 28px; background: var(--purple);
    display: flex; justify-content: flex-end; align-items: stretch; padding-right: 60px;
  }
  .main-nav a {
    color: var(--white); font-size: 11px; font-weight: 700; text-decoration: none;
    display: flex; align-items: center; padding: 0 11px; letter-spacing: 0.2px;
  }
  .main-nav a.is-active { background: var(--green-active); }

  .hero {
    height: 300px;
    background:
      radial-gradient(ellipse 40% 70% at 72% 40%, var(--hero-light) 0%, rgba(200,228,180,0) 70%),
      linear-gradient(100deg, var(--hero-dark) 0%, var(--hero-mid) 45%, #7fa779 65%, var(--hero-dark) 100%);
  }

  .intro { display: flex; padding: 22px 70px 0 150px; gap: 60px; }
  .cycle { flex: 0 0 200px; margin-top: 4px; }
  .intro-copy { flex: 1; }
  .intro-title { font-size: 29px; font-weight: 400; color: var(--purple); line-height: 1.12; margin-bottom: 14px; }
  .intro-copy p { font-size: 13px; line-height: 1.55; margin-bottom: 11px; }
  .intro-copy strong { font-weight: 700; }
  .cycle text { font-family: "Lato", Arial, sans-serif; }
</style>
</head>
<body>
<div class="page">
  <header class="site-header">
    <div class="brand">
      <span class="brand-name">Brunexa Group</span>
      <span class="brand-mark"></span>
    </div>
    <div class="header-links">
      <a class="speaker-link" href="#">HIRE MARISOL TO SPEAK</a>
      <span class="phone">+1 555 014 2200</span>
    </div>
  </header>

  <nav class="main-nav">
    <a href="#">ABOUT</a>
    <a href="#">WHAT WE DO</a>
    <a href="#">LEAD GENERATION</a>
    <a href="#">PROSPECTING</a>
    <a href="#" class="is-active">HIRING &amp; ONBOARDING</a>
    <a href="#">RESOURCES</a>
    <a href="#">EVENTS</a>
    <a href="#">BLOG</a>
    <a href="#">CONTACT</a>
  </nav>

  <div class="hero" role="img" aria-label="Green-toned photo of a businessman seen from behind facing a wall of chalk sketches: marketing, communications, new markets, charts and arrows"></div>

  <section class="intro">
    <svg class="cycle" width="200" height="190" viewBox="0 0 200 190" aria-label="Revenue Generating System cycle">
      <circle cx="100" cy="98" r="62" fill="none" stroke="var(--grey-light)" stroke-width="5"/>
      <circle cx="100" cy="34" r="30" fill="var(--grey)" stroke="var(--white)" stroke-width="3"/>
      <text x="100" y="30" font-size="7" fill="#fff" text-anchor="middle" font-weight="700">LEAD</text>
      <text x="100" y="40" font-size="7" fill="#fff" text-anchor="middle" font-weight="700">GENERATION</text>
      <circle cx="40" cy="148" r="30" fill="var(--grey)" stroke="var(--white)" stroke-width="3"/>
      <text x="40" y="151" font-size="7" fill="#fff" text-anchor="middle" font-weight="700">PROSPECTING</text>
      <circle cx="160" cy="148" r="30" fill="var(--teal)" stroke="var(--white)" stroke-width="3"/>
      <text x="160" y="146" font-size="7" fill="#fff" text-anchor="middle" font-weight="700">HIRING &amp;</text>
      <text x="160" y="156" font-size="7" fill="#fff" text-anchor="middle" font-weight="700">ONBOARDING</text>
      <text x="100" y="92" font-size="13" fill="var(--grey)" text-anchor="middle">Revenue</text>
      <text x="100" y="107" font-size="13" fill="var(--grey)" text-anchor="middle">Generating</text>
      <text x="100" y="122" font-size="13" fill="var(--grey)" text-anchor="middle">System</text>
    </svg>

    <div class="intro-copy">
      <h1 class="intro-title">The Brunexa Group Approach to Sales and Marketing<br>Hiring and Onboarding</h1>
      <p>The average sales person takes between nine to twelve months to reach full productivity. The average marketing person takes three to six months to reach full productivity. <strong>These numbers may shock you, but they're simply true.</strong></p>
      <p>Without ensuring that you made the right selection in the hiring process and a well thought out training onboarding plan, <strong>your new sales rep may never reach their full selling potential</strong> – no matter how much sales experience they have. <strong>And your marketing staffer may quit before they reach their third month.</strong></p>
      <p>But of course, that <u>doesn't</u> mean you have to wait until the worst happens to know if your new hire is going to cut it.</p>
      <p>We are not recruiters. <strong>We guide you through developing and implementing a successful hiring process</strong> to add staff that fit your company culture and get you the sales and lead generation results required to meet your goals.</p>
    </div>
  </section>
</div>
</body>
</html>
```